Larkspur Talent IT Recruiting firm needs a business card design for Recruiters, Sourcers, and Account

We need business cards that allow us to change all contact info, names, titles (Recruiter, Sourcer, Account Manager, Director, CEO, etc) per person since we have three offices, in three cities, Phoenix, Austin, and Las Vegas. We do recruiting and contractors for IT positions (Developers, Architects, Software Engineers, Security Engineers, Help Desk, DBAs, PMs, Scrum Masters, etc.) Our client companies are very diverse from Meridian 100 to silicone Valley type start-ups.

So, while we what hip, techie, and quirky, it still needs to be professional. Primary color we use is blue, with silver as a secondary color.

Target Market(s)

IT, Technology

Industry/Entity Type

Business

Contact Information for Business Card

Company name: Larkspur Talent, Inc.
Website: www.larkspurtalent.example
Logos for Careerloop, Blipster, and Myriada

Name, Title, Office Number, Cell Number, email

Font styles to use
Serif
Sans Serif

Colors
0455a3
d5d5d5

Requirements
Nice to have
• The grey I selected below is not necessary - but, would like silver included. I included a card design (File 3: LTI early trial example.jpg) that I had started on. It's very rough, and not quite what we're looking for, but what we did like is the logo, big, maybe a bit faded, off center, goes out of frame, etc. Still looking for other ideas - you are the pros! But, just an idea of a design element we liked.

```html
<!DOCTYPE html>
<html lang="en">
<head>
<meta charset="utf-8">
<title>Larkspur Talent — Business Card</title>
<link href="https://fonts.googleapis.com/css2?family=Marcellus&family=Open+Sans:wght@400&family=Alegreya+Sans:wght@400&display=swap" rel="stylesheet">
<style>
  :root {
    --backdrop: #1b1b1b;
    --card-white: #ffffff;
    --card-grey: #555555;
    --ink: #2a2a2a;
    --ink-soft: #4a4a4a;
    --brand-blue: #0455a3;
    --brand-sky: #1b8fdc;
    --silver: #d5d5d5;
    --white: #ffffff;
  }
  * { box-sizing: border-box; margin: 0; padding: 0; }
  html, body {
    width: 1200px; height: 907px; overflow: hidden;
    background: var(--backdrop);
  }
  .stage { position: relative; width: 1200px; height: 907px; }
  .card {
    position: absolute; left: 300px; width: 600px; height: 343px; overflow: hidden;
  }
  .card--front { top: 98px; background: var(--card-white); }
  .card--back { top: 475px; background: var(--card-grey); }

  .wordmark {
    position: absolute; left: 43px; top: 66px;
    font-family: "Marcellus", serif; font-size: 31px; line-height: 1;
    letter-spacing: 1px; white-space: nowrap; color: var(--ink);
  }

  .contact {
    position: absolute; left: 40px; top: 209px; list-style: none;
    font-family: "Open Sans", sans-serif; font-size: 14.5px; color: var(--ink-soft);
  }
  .contact li { display: flex; align-items: center; height: 22.7px; white-space: nowrap; }
  .contact svg { width: 14px; height: 14px; margin-right: 9px; fill: var(--brand-blue); flex: none; }

  .nameplate {
    position: absolute; left: 312px; top: 211px; width: 288px; height: 88px;
    background: linear-gradient(180deg, var(--brand-sky), var(--brand-blue));
    border-radius: 44px 0 0 44px;
    font-family: "Alegreya Sans", sans-serif; color: var(--white);
  }
  .nameplate__dot {
    position: absolute; left: 8px; top: 8px; width: 72px; height: 72px;
    border-radius: 50%; background: var(--white);
  }
  .nameplate__name {
    position: absolute; right: 42px; top: 14px; font-size: 24px; line-height: 1.2; white-space: nowrap;
  }
  .nameplate__title {
    position: absolute; right: 42px; top: 48px; font-size: 18px; line-height: 1.2; white-space: nowrap;
  }

  .emblem {
    position: absolute; left: 199px; top: 81px; width: 196px; height: 196px;
    border-radius: 50%; background: var(--white);
    display: flex; flex-direction: column; align-items: center; justify-content: center;
  }
  .emblem__name {
    font-family: "Marcellus", serif; font-size: 19px; letter-spacing: 1px;
    color: var(--card-grey); text-align: center; line-height: 1.2;
  }
  .social {
    display: flex; gap: 8px; margin-top: 18px; list-style: none;
    font-family: "Open Sans", sans-serif; font-size: 9.5px; color: var(--brand-blue);
  }
  .social li { display: flex; align-items: center; gap: 3px; }
  .social li::before {
    content: ""; width: 10px; height: 10px; border-radius: 2px; background: var(--brand-blue);
  }
</style>
</head>
<body>
<main class="stage">
  <section class="card card--front" aria-label="Card front">
    <div class="wordmark">LARKSPUR TALENT</div>

    <ul class="contact">
      <li>
        <svg viewBox="0 0 16 16" aria-hidden="true"><path d="M4 1l3 3-2 2c1 2 3 4 5 5l2-2 3 3-2 3C7 15 1 9 1 3z"/></svg>
        555-014-2290
      </li>
      <li>
        <svg viewBox="0 0 16 16" aria-hidden="true"><path d="M4 0h8v16H4zM5.5 2v6h5V2zM5.5 10v1.5h1.5V10zM7.3 10v1.5h1.5V10zM9 10v1.5h1.5V10zM5.5 12.5V14h1.5v-1.5zM7.3 12.5V14h1.5v-1.5zM9 12.5V14h1.5v-1.5z"/></svg>
        555-017-6631
      </li>
      <li>
        <svg viewBox="0 0 16 16" aria-hidden="true"><path d="M1 3h14v10H1zM2.5 4.5v.5L8 9l5.5-4v-.5zM2.5 6.5v5h11v-5L8 10.5z"/></svg>
        info@larkspurtalent.example
      </li>
      <li>
        <svg viewBox="0 0 16 16" aria-hidden="true"><path d="M8 1a7 7 0 100 14A7 7 0 008 1zm0 1.3c.8.8 1.4 2.2 1.6 3.7H6.4C6.6 4.5 7.2 3.1 8 2.3zM2.4 7.3h2.7c0 .5 0 1 .1 1.4H2.4a5.7 5.7 0 010-1.4zm4 0h3.2a8 8 0 010 1.4H6.4a8 8 0 010-1.4zm4.5 0h2.7a5.7 5.7 0 010 1.4h-2.8c.1-.4.1-.9.1-1.4zM6.4 10h3.2c-.2 1.5-.8 2.9-1.6 3.7-.8-.8-1.4-2.2-1.6-3.7z"/></svg>
        www.larkspurtalent.example
      </li>
    </ul>

    <div class="nameplate">
      <span class="nameplate__dot" aria-hidden="true"></span>
      <span class="nameplate__name">Dana Whitfield</span>
      <span class="nameplate__title">Manager</span>
    </div>
  </section>

  <section class="card card--back" aria-label="Card back">
    <div class="emblem">
      <span class="emblem__name">LARKSPUR<br>TALENT</span>
      <ul class="social">
        <li>Careerloop</li>
        <li>Blipster</li>
        <li>Myriada</li>
      </ul>
    </div>
  </section>
</main>
</body>
</html>
```